I need a business card design for a new business based in South West Australia.
I specialize in residential window cleaning & general handyman maintenance.

Dale Marsh - 412 SILVER HAWK DETAILING
- Window Cleaning
- House Maintenance

```html
<!DOCTYPE html>
<html lang="en">
<head>
<meta charset="utf-8">
<title>Silver Hawk Detailing – Business Card</title>
<link rel="stylesheet" href="https://fonts.googleapis.com/css2?family=Open+Sans:wght@400;600;800&display=swap">
<style>
  :root {
    --backdrop: #3b3531;
    --card-white: #ffffff;
    --brand-blue: #1a5fb4;
    --brand-blue-deep: #0b4fa8;
    --brand-blue-light: #1f6fd0;
    --accent-orange: #f26b1d;
    --ink: #2a2a2a;
  }
  * { box-sizing: border-box; margin: 0; padding: 0; }
  html, body { width: 1200px; height: 844px; overflow: hidden; }
  body {
    background: var(--backdrop);
    font-family: "Open Sans", Arial, sans-serif;
    position: relative;
  }
  .card {
    position: absolute;
    top: 262px;
    width: 520px;
    height: 300px;
    border-radius: 3px;
    box-shadow: 0 10px 24px rgba(0,0,0,.45);
  }
  .card--front { left: 50px; background: var(--card-white); }
  .card--back {
    left: 630px;
    background: linear-gradient(160deg, var(--brand-blue-light), var(--brand-blue-deep));
  }
  .brand { position: absolute; }
  .brand__name {
    font-weight: 800;
    font-size: 27px;
    letter-spacing: -0.5px;
    line-height: 1;
    text-transform: uppercase;
  }
  .brand__tagline {
    font-weight: 800;
    font-size: 11.5px;
    letter-spacing: .6px;
    text-transform: uppercase;
    margin-top: 5px;
  }
  .card--front .brand { right: 28px; top: 40px; text-align: left; }
  .card--front .brand__name { color: var(--brand-blue); }
  .card--front .brand__tagline { color: var(--accent-orange); }
  .card--back .brand { right: 30px; top: 150px; }
  .card--back .brand__name,
  .card--back .brand__tagline { color: var(--card-white); }
  .contact {
    position: absolute;
    left: 30px;
    top: 150px;
    color: var(--ink);
    font-size: 13.5px;
    line-height: 1.35;
  }
  .contact__name {
    color: var(--brand-blue);
    font-weight: 600;
    font-size: 19px;
    line-height: 1.1;
  }
  .contact__role { margin-bottom: 20px; }
  .contact__address { margin-bottom: 16px; }
  .label { color: var(--brand-blue); }
  .web { color: var(--brand-blue); margin-left: 8px; }
  .gap { margin-left: 6px; }
</style>
</head>
<body>
  <section class="card card--front" aria-label="Business card front">
    <div class="brand">
      <div class="brand__name">Silver Hawk Detailing</div>
      <div class="brand__tagline">Window Cleaning &amp; House Maintenance</div>
    </div>
    <div class="contact">
      <div class="contact__name">Dale Marsh</div>
      <div class="contact__role">Managing Director</div>
      <div class="contact__address">1234, Address GoesHere, Country, 12345</div>
      <div><span class="label">T:</span>(044) 123 456 789 <span class="label gap">F:</span>(044) 123456789 <span class="label gap">M:</span>(044)123456789</div>
      <div><span class="label">E:</span>info@youremail.com <span class="web">www.yourweb.com</span></div>
    </div>
  </section>

  <section class="card card--back" aria-label="Business card back">
    <div class="brand">
      <div class="brand__name">Silver Hawk Detailing</div>
      <div class="brand__tagline">Window Cleaning &amp; House Maintenance</div>
    </div>
  </section>
</body>
</html>
```